Business Cards for IT Consulting Company (Managed Service Provider)

I am looking to have some business cards printed and would like some designs. We are an IT Consulting company based in Vancouver BC. I would like a nice clean and modern look to the cards. I have uploaded all the versions of my logo so parts can be used as needed. Here is a snippit from our website homepage:

Quillbrook Networks Ltd. is an IT Solutions Partner located in Vancouver BC, Canada. We offer IT solutions and support to customers in the greater Vancouver Area. With expertise in Microsoft platforms, as well as Linux and Mac OSX and over 12 years experience in the IT industry, Quillbrook Networks is dedicated to offering our clients top quality service and products. We take pride in the solutions we offer our customers. The greatest compliment a client can give us is to recommend our services.

Quillbrook Networks Ltd. offers a wide range of IT services from onsite service to remote support and managed service solutions. This allows clients to choose the support path that best suits their company’s needs. Supporting many different sized companies from small to enterprise level over the past 12 years Quillbrook Networks has the experience and expertise needed to ensure things run smoothly. Allowing our clients to focus on doing business.

Revolutionizing the way IT services are delivered.

Quillbrook Networks is dedicated to providing our clients with IT solutions that work and grow with them for years to come. This philosophy helps save money in the long run instead of replacing equipment constantly. Far too often IT solutions are not well thought out and while possibly solving the problem at hand, require replacement due to growth or quality within a very short time frame. Quillbrook Networks takes pride in providing solutions that will last and be able to accommodate growth without the need for replacement.

Industry/Entity Type

Information Technology

Contact Information for Business Card

Quillbrook Networks Ltd.
(Employee Name)
Eml: (Employees Email Address)
Web: quillbrook.me
Ph: 604-555-0148

Font styles to use
Serif
Sans Serif

Requirements
Must have
• The Company logo and company colors.
Nice to have
• - Our tag line: "Revolutionizing IT Services" or "Revolutionizing the way IT services are delivered."
• - Also I really like the idea of nature and technology together blending which is sort of where my logo came from so integrating that somehow onto the business cards would be great.

```html
<!DOCTYPE html>
<html lang="en">
<head>
<meta charset="utf-8">
<title>Quillbrook Networks Ltd. – Business Card</title>
<link rel="stylesheet" href="https://fonts.googleapis.com/css2?family=Montserrat:ital,wght@0,400;0,500;0,600;1,400&family=Roboto:ital,wght@0,400;0,500;1,400&display=swap">
<style>
  :root {
    --backdrop: #a9a7a7;
    --card: #1c1c1c;
    --card-pattern: #202020;
    --brand-blue: #1e8fd6;
    --text-light: #e6e6e6;
    --text-muted: #b4b4b4;
  }
  * { margin: 0; padding: 0; box-sizing: border-box; }
  html, body { width: 1200px; height: 1200px; overflow: hidden; }
  body {
    position: relative;
    background: var(--backdrop);
    font-family: "Montserrat", sans-serif;
  }
  .card {
    position: absolute;
    left: 238px;
    width: 713px;
    height: 420px;
    background: var(--card);
  }
  .card-front { top: 117px; }
  .card-back { top: 643px; }

  /* Front */
  .front-pattern {
    position: absolute; inset: 0;
    background: var(--card-pattern);
  }
  .brand-lockup {
    position: absolute;
    left: 110px; top: 152px;
    display: flex; align-items: center; gap: 22px;
  }
  .brand-dot {
    width: 70px; height: 70px;
    border: 3px solid var(--brand-blue);
    border-radius: 50%;
  }
  .brand-name {
    color: var(--brand-blue);
    font-weight: 600;
    line-height: 1;
  }
  .brand-name .word { display: block; font-size: 62px; letter-spacing: -0.5px; }
  .brand-name .suffix { display: block; font-size: 23px; letter-spacing: 1px; margin-top: 8px; }
  .tagline {
    position: absolute;
    left: 0; right: 0; top: 377px;
    display: flex; align-items: center; justify-content: center; gap: 16px;
    color: var(--text-light);
    font-size: 19px; font-weight: 400;
  }
  .tagline-rule {
    width: 110px; height: 3px;
    background: linear-gradient(90deg, transparent, var(--brand-blue) 25%);
  }
  .tagline-rule.right { background: linear-gradient(270deg, transparent, var(--brand-blue) 25%); }

  /* Back */
  .back-decoration {
    position: absolute;
    left: 285px; top: 22px; width: 395px; height: 370px;
    background: var(--card-pattern);
    border-radius: 8px;
  }
  .back-brand {
    position: absolute;
    left: 60px; top: 188px; width: 235px;
    text-align: center;
    color: var(--brand-blue);
    font-size: 34px; font-weight: 600;
  }
  .divider {
    position: absolute;
    left: 339px; top: 82px;
    width: 2px; height: 255px;
    background: linear-gradient(180deg, transparent, #d8d8d8 20%, #d8d8d8 80%, transparent);
  }
  .person {
    position: absolute;
    left: 399px; top: 128px;
    font-family: "Roboto", sans-serif;
  }
  .person-name { color: var(--brand-blue); font-family: "Montserrat", sans-serif; font-size: 25px; font-weight: 600; }
  .person-role { color: var(--text-muted); font-size: 16px; font-style: italic; margin-top: 4px; }
  .contact-list { list-style: none; margin-top: 26px; }
  .contact-list li {
    display: flex; align-items: center; gap: 16px;
    color: var(--text-light); font-size: 18px;
    height: 27px;
  }
  .contact-list svg { width: 18px; height: 18px; fill: var(--brand-blue); flex: none; }
</style>
</head>
<body>
  <section class="card card-front">
    <div class="front-pattern" role="img" aria-label="Subtle dark geometric background pattern"></div>
    <div class="brand-lockup">
      <span class="brand-dot"></span>
      <div class="brand-name">
        <span class="word">Quillbrook</span>
        <span class="suffix">NETWORKS LTD.</span>
      </div>
    </div>
    <div class="tagline">
      <span class="tagline-rule"></span>
      <span>Revolutionizing IT Services</span>
      <span class="tagline-rule right"></span>
    </div>
  </section>

  <section class="card card-back">
    <div class="back-decoration" role="img" aria-label="Faint large geometric decoration"></div>
    <div class="back-brand">Quillbrook</div>
    <div class="divider"></div>
    <div class="person">
      <p class="person-name">Daniel Hart</p>
      <p class="person-role">Managing Director</p>
      <ul class="contact-list">
        <li>
          <svg viewBox="0 0 24 24" aria-hidden="true"><path d="M3 8c0-3 4-4 9-4s9 1 9 4v2h-5V8H8v2H3zM6 11h12l3 9H3z"/></svg>
          604-555-0148
        </li>
        <li>
          <svg viewBox="0 0 24 24" aria-hidden="true"><path d="M12 2a10 10 0 100 20 10 10 0 000-20zm0 2c1 1 2 3 2.4 6H9.6C10 7 11 5 12 4zM4.3 10h3.3a15 15 0 000 4H4.3a8 8 0 010-4zm5.3 4a13 13 0 010-4h4.8a13 13 0 010 4zm6.8 0a15 15 0 000-4h3.3a8 8 0 010 4zM12 20c-1-1-2-3-2.4-6h4.8C14 17 13 19 12 20z"/></svg>
          www.quillbrook.me
        </li>
        <li>
          <svg viewBox="0 0 24 24" aria-hidden="true"><path d="M2 5h20v14H2zm2 2v.5l8 6 8-6V7zm0 3v7h16v-7l-8 6z"/></svg>
          support@quillbrook.me
        </li>
      </ul>
    </div>
  </section>
</body>
</html>
```